Webdesign für Hunde- und Katzenernährungsberatung
Zielgruppe
Hunde und Katzenernährungsberatung, für Menschen, die auch bei ihren Hunden und Katzen auf gesunde, natürliche Ernährung achten wollen, ohne unnötigen Geschmacksverstärker, Zucker, Zusatzstoffe, etc. die gesundheitliche Probleme bei den Tieren verursachen können.
Umstellung auf natürliche, artgerechte Fütterung, teils roh, teils gekocht, angepasst auf Grösse, Rasse, Alter etc., auch speziell für Welpen
Beratung bei:
Übergewicht
Allergien
Unverträglichkeiten
Magen-Darm Problemen
individuelle Ernährungspläne
Selbsthergestellte Kekse, Leckerlies, Snacks, Pralinen und div. Hausmannskost in Einmachgläsern (alles auf Vorbestellung).
Diverse Accessoires
Halsbänder, Leinen, Geschirr aus div. natürlichen Materialien
Lern- und Spielzeug aus Holz und Stoff
div. Zubehör für Tiere, sowie auch für Frauchen und Herrchen
Aufgabenstellung
Die Seite sollte stilvoll aber nicht überfüllt sein und im Retro/Vintage Stil gehalten werden, da das Logo bereits sehr wirksam und eher auffällig ist, dezente Töne im Hintergrund, die Nahrungsmittel werden dann ev. auf Schieferplatten oder unauffälligem Hintergrund platziert. Ich sollte zu einem späteren Zeitpunkt selber Fotos, Links, Texte, etc. einfach dazu fügen können.

```html
<!DOCTYPE html>
<html lang="de">
<head>
<meta charset="utf-8">
<title>Pfotenwerk – Ernährungsberatung</title>
<link rel="stylesheet" href="https://fonts.googleapis.com/css2?family=Fira+Sans+Extra+Condensed:wght@300;400&family=Figtree:ital,wght@0,400;0,500;1,400&family=Playfair+Display:ital,wght@1,400;1,700&display=swap">
<style>
:root{
  --green:#93c462;
  --brown:#7b4a2d;
  --orange:#e8663d;
  --blue:#8ec3dd;
  --text:#3b3b3b;
  --muted:#777;
  --paper:#f6f5f3;
  --white:#ffffff;
  --cond:"Fira Sans Extra Condensed",sans-serif;
  --body:"Figtree",sans-serif;
}
*{margin:0;padding:0;box-sizing:border-box}
html,body{width:1079px;height:1200px;overflow:hidden}
body{position:relative;background:var(--paper);font-family:var(--body);color:var(--text)}
a{text-decoration:none;color:inherit}
h1,h2,h3,h4{font-weight:400}

/* header */
.site-header{position:absolute;left:0;top:0;width:1079px;height:84px;background:var(--white);z-index:3;border-top:3px solid var(--blue)}
.brand{position:absolute;left:90px;top:-3px;width:120px;height:124px;border-radius:0 0 60px 60px;background:var(--white);display:flex;align-items:center;justify-content:center;gap:6px;z-index:4;text-decoration:none}
.brand-dot{width:10px;height:10px;border-radius:50%;background:var(--blue)}
.brand-name{font-family:var(--cond);font-weight:400;font-size:21px;color:var(--blue);text-decoration:none}
.main-nav a{position:absolute;top:42px;font-family:var(--cond);font-weight:300;font-size:15px;color:var(--text);white-space:nowrap}
.main-nav a.active{color:var(--brown);font-weight:400}
.main-nav a.shop{color:var(--orange);font-weight:400}
.nav-note{position:absolute;left:664px;top:31px;font-family:var(--cond);font-size:9px;color:var(--blue)}
.nav-pointer{position:absolute;left:419px;top:84px;width:0;height:0;border-left:9px solid transparent;border-right:9px solid transparent;border-top:7px solid var(--white);z-index:3}
.btn{display:flex;align-items:center;justify-content:center;background:var(--green);color:var(--white);font-family:var(--cond);font-weight:400;border-radius:4px;box-shadow:0 0 0 2px var(--white),0 0 0 3px var(--green)}
.btn-contact{position:absolute;left:942px;top:21px;width:116px;height:30px;font-size:15px}
.contact-note{position:absolute;left:972px;top:59px;font-family:var(--cond);font-size:9px;color:var(--green)}

/* hero */
.hero{position:absolute;left:0;top:84px;width:1079px;height:262px;background:linear-gradient(180deg,#d9d4c8 0%,#c9c2b4 55%,#b9c25a 80%,#c4a98a 100%)}
.hero-dots{position:absolute;left:1049px;top:176px;display:flex;flex-direction:column;gap:4px}
.hero-dots span{width:7px;height:7px;border-radius:50%;border:1px solid var(--white)}
.hero-dots span.on{background:var(--white)}
.hero-badge{position:absolute;left:464px;top:296px;width:152px;height:76px;border-radius:76px 76px 0 0;background:var(--paper);display:flex;justify-content:center;padding-top:20px}

/* intro */
.page-title{position:absolute;left:184px;top:381px;font-family:var(--cond);font-size:34px;color:var(--green)}
.page-sub{position:absolute;left:184px;top:424px;font-family:var(--cond);font-weight:300;font-size:17px}
.intro-text{position:absolute;left:184px;top:459px;width:392px;font-size:10.5px;line-height:13.5px;text-align:justify}
.quote{position:absolute;left:190px;top:596px;width:312px}
.quote-text{font-style:italic;font-size:11.5px;padding-left:17px}
.quote-mark{position:absolute;font-family:var(--cond);font-size:28px;color:var(--green);font-style:italic;line-height:1}
.quote-author{text-align:right;font-style:italic;font-size:10px;color:var(--green);margin-top:6px}
.quote-role{text-align:right;font-size:8px;color:var(--muted);margin-top:4px;line-height:10.5px}

.avoid-title{position:absolute;left:613px;top:460px;font-size:12.5px;font-weight:500}
.avoid-list{position:absolute;left:620px;top:487px;list-style:none}
.avoid-list li{display:flex;align-items:center;gap:7px;height:29.3px;font-size:11.5px}
.promise{position:absolute;left:614px;top:615px;width:282px;height:74px;background:var(--green);border-radius:4px;box-shadow:0 0 0 2px var(--paper),0 0 0 3px var(--green);color:var(--white);padding:10px 14px}
.promise h3{font-family:var(--cond);font-size:18px}
.promise p{font-size:9.5px;line-height:12.5px;margin-top:3px}

/* process */
.process-title{position:absolute;left:184px;top:684px;font-family:var(--cond);font-size:20px;color:var(--green)}
.process-sub{position:absolute;left:184px;top:708px;font-family:var(--cond);font-weight:300;font-size:14.5px}
.step{position:absolute;top:747px;width:190px;text-align:center}
.step-icon{width:66px;height:66px;border-radius:50%;border:2px solid var(--green);margin:0 auto;background:#eaf2df}
.step h4{font-family:var(--cond);font-size:15px;color:var(--green);margin-top:9px}
.step .lead{font-size:10.5px;line-height:13.5px}
.step .small{font-size:8px;line-height:10.5px;margin-top:1px}
.step .ok{font-size:10.5px;color:var(--green);margin-top:14px}
.arrow{position:absolute;top:771px}
.btn-offer{position:absolute;left:432px;top:941px;width:215px;height:35px;font-size:15px}

.tagline{position:absolute;left:0;top:1031px;width:1079px;text-align:center}
.tagline strong{font-family:"Playfair Display",serif;font-style:italic;font-weight:700;font-size:16px;color:var(--text)}
.tagline span{display:block;font-family:"Playfair Display",serif;font-style:italic;font-weight:400;font-size:9px;color:var(--blue);margin-top:1px}

/* footer */
.site-footer{position:absolute;left:0;top:1095px;width:1079px;height:105px;background:var(--white)}
.footer-brand{position:absolute;left:62px;top:38px;display:flex;align-items:center;gap:4px}
.footer-brand .brand-name{font-size:13px;color:#9a9a9a}
.footer-brand .brand-dot{width:7px;height:7px;background:#9a9a9a}
.copyright{position:absolute;left:143px;top:38px;font-family:var(--cond);font-size:13px}
.footer-nav a{position:absolute;top:38px;font-family:var(--cond);font-size:13px;color:var(--text)}
.footer-nav a.shop{color:var(--orange)}
</style>
</head>
<body>

<header class="site-header">
  <a class="brand" href="#"><span class="brand-dot"></span><span class="brand-name">Pfotenwerk</span></a>
  <nav class="main-nav">
    <a href="#" style="left:297px">Startseite</a>
    <a href="#" class="active" style="left:370px">Ernährungsberatung</a>
    <a href="#" style="left:507px">Futter</a>
    <a href="#" style="left:562px">Accessoires</a>
    <a href="#" class="shop" style="left:647px">Onlineshop</a>
  </nav>
  <span class="nav-note">Mhmm, lecker!</span>
  <a class="btn btn-contact" href="#">Kontakt</a>
  <span class="contact-note">Wir beißen nicht.</span>
</header>
<div class="nav-pointer"></div>

<section class="hero" role="img" aria-label="Foto: Katze und Hund fressen aus grünen Näpfen mit Fleisch und Gemüse">
  <div class="hero-dots"><span class="on"></span><span></span><span></span></div>
</section>
<div class="hero-badge">
  <svg width="56" height="54" viewBox="0 0 56 54" aria-hidden="true">
    <path d="M14 38 C2 30 4 12 14 2 C22 14 24 30 14 38Z" fill="var(--green)"/>
    <path d="M18 44 C26 28 44 24 56 30 C48 44 32 50 18 44Z" fill="var(--green)"/>
    <path d="M10 52 C14 44 20 40 30 36" stroke="var(--green)" stroke-width="2.5" fill="none"/>
  </svg>
</div>

<main>
  <h1 class="page-title">Ernährungsberatung</h1>
  <p class="page-sub">Damit es ihren Liebsten gut geht.</p>
  <p class="intro-text">Lorem ipsum dolor sit amet, consetetur sadipscing elitr, sed diam nonumy eirmod tempor invidunt ut labore et dolore magna aliquyam erat, sed diam voluptua. At vero eos et accusam et justo duo dolores et ea rebum. Stet clita kasd gubergren, no sea takimata sanctus est Lorem ipsum dolor sit amet. Lorem ipsum dolor sit amet, consetetur sadipscing elitr, sed diam nonumy eirmod tempor invidunt ut labore et dolore magna aliquyam erat, sed diam voluptua. At vero eos et accusam et justo duo dolores et ea rebum. Stet clita kasd gubergren, no sea takimata sanctus est Lorem ipsum dolor sit amet.</p>

  <blockquote class="quote">
    <span class="quote-mark" style="left:318px;top:-12px">“</span>
    <span class="quote-mark" style="left:4px;top:16px">„</span>
    <p class="quote-text">Gemeinsam lösen wir das Problem oder beugen es vor!</p>
    <p class="quote-author">Ihre Lena Marbach</p>
    <p class="quote-role">Geprüfte Ernährungsberaterin für<br>Haustiere</p>
  </blockquote>

  <h2 class="avoid-title">Wir verzichten in den Ernährungsplänen auf:</h2>
  <ul class="avoid-list">
    <li><svg width="13" height="13" viewBox="0 0 13 13"><path d="M1 1L12 12M12 1L1 12" stroke="var(--green)" stroke-width="2.2"/></svg>Unnötige Geschmacksverstärker</li>
    <li><svg width="13" height="13" viewBox="0 0 13 13"><path d="M1 1L12 12M12 1L1 12" stroke="var(--green)" stroke-width="2.2"/></svg>Zucker</li>
    <li><svg width="13" height="13" viewBox="0 0 13 13"><path d="M1 1L12 12M12 1L1 12" stroke="var(--green)" stroke-width="2.2"/></svg>Zusatzstoffe</li>
    <li><svg width="13" height="13" viewBox="0 0 13 13"><path d="M1 1L12 12M12 1L1 12" stroke="var(--green)" stroke-width="2.2"/></svg>Chemische Produkte</li>
  </ul>
  <div class="promise">
    <h3>Unser Versprechen.</h3>
    <p>Ausschließlich natürliche Produkte und Zutaten sowie ein ökologisch nachvollziehbare Gerichte.</p>
  </div>

  <h2 class="process-title">Unser gemeinsamer Ablaufplan</h2>
  <p class="process-sub">Schritt für Schritt kommen wir der Ursache gemeinsam näher.</p>

  <div class="step" style="left:158px">
    <div class="step-icon" role="img" aria-label="Illustration: Katze und Hund"></div>
    <h4>Diagnose</h4>
    <p class="lead">Wir finden die Ursache:</p>
    <p class="small">Übergewicht, Allergie,<br>Unverträglichkeit, Magen-Darm-<br>Problem, usw.</p>
  </div>
  <svg class="arrow" style="left:387px" width="24" height="20" viewBox="0 0 24 20"><path d="M0 7H12V1L24 10L12 19V13H0Z" fill="var(--brown)"/></svg>
  <div class="step" style="left:445px">
    <div class="step-icon" role="img" aria-label="Illustration: Futternapf mit Gras"></div>
    <h4>Umstellung/Ernährungsplan</h4>
    <p class="lead">Erstellung eines individuellen<br>Ernährungsplanes und<br>Umstellung auf:</p>
    <p class="small">natürliche, artgerechte Fütterung, teils<br>roh, teils gekocht, angepasst auf Größe,<br>Rasse, Alter, Gewicht usw.</p>
  </div>
  <svg class="arrow" style="left:668px" width="24" height="20" viewBox="0 0 24 20"><path d="M0 7H12V1L24 10L12 19V13H0Z" fill="var(--brown)"/></svg>
  <div class="step" style="left:715px">
    <div class="step-icon" role="img" aria-label="Illustration: Futternapf mit Gras"></div>
    <h4>Beobachtung/Erfolgreich</h4>
    <p class="lead">Regelmäßige Beobachtung und<br>Kontroller über das verbesserte<br>Verhalten des Tieres.</p>
    <p class="ok">Beratung war erfolgreich.</p>
  </div>

  <a class="btn btn-offer" href="#">Unverbindliches Angebot anfordern</a>

  <p class="tagline"><strong>Wir <svg width="13" height="11" viewBox="0 0 13 11"><path d="M6.5 11L1 5.5A3 3 0 0 1 6.5 1.5A3 3 0 0 1 12 5.5Z" fill="var(--blue)"/></svg> Tiere.</strong><span>Hunde, Katzen und mehr</span></p>
</main>

<footer class="site-footer">
  <div class="footer-brand"><span class="brand-dot"></span><span class="brand-name">Pfotenwerk</span></div>
  <p class="copyright">Copyright © 2017 pfotenwerk.ch</p>
  <nav class="footer-nav">
    <a href="#" style="left:368px">Impressum</a>
    <a href="#" style="left:435px">Kontakt</a>
    <a href="#" style="left:489px">Datenschutz</a>
    <a href="#" style="left:562px">AGBs</a>
    <a href="#" class="shop" style="left:605px">Onlineshop</a>
  </nav>
</footer>

</body>
</html>
```